Harbourline Electrical Solutions

On one side. LOGO (underneath:) Commercial Industrial Residential

- NAME & CONTACT DETAILS

Marcus T. Hollings
Project Manager

(Cell icon) (441) 555-0187
(Email icon) hlelectricalsolutions@mailvento.com
(Facebook & Instagram icons )@hlelectricalsolutions

Other side: LOGO - underneath ELECTRICAL CONSTRUCTION & MAINTENANCE . LED LIGHTING & AUTOMATION . LIFE SAFETY SYSTEMS (FIRE ALARM / SECURITY) . DATA & COMMUNICATION

```html
<!DOCTYPE html>
<html lang="en">
<head>
<meta charset="utf-8">
<title>Harbourline Electrical Solutions — Business Card</title>
<link href="https://fonts.googleapis.com/css2?family=Montserrat:wght@400;500;600;700&display=swap" rel="stylesheet">
<style>
  :root {
    --teal: #145a6d;
    --teal-deep: #0f4d5e;
    --white: #ffffff;
    --rule: #4a4a4a;
    --backdrop: #e4e4e4;
    --text-soft: #dfeef2;
  }
  * { box-sizing: border-box; margin: 0; padding: 0; }
  html, body {
    width: 1200px; height: 930px; overflow: hidden;
    background: var(--backdrop);
    font-family: "Montserrat", sans-serif;
  }
  .canvas { position: relative; width: 1200px; height: 930px; }

  .card {
    position: absolute;
    width: 560px; height: 320px;
    border-radius: 22px;
    overflow: hidden;
    box-shadow: 0 6px 18px rgba(0,0,0,0.18);
  }

  /* Back side */
  .card-back {
    left: 60px; top: 110px;
    background: var(--teal);
    color: var(--white);
    padding: 62px 56px;
  }
  .brand {
    display: flex; align-items: center; gap: 14px;
  }
  .brand-mark {
    width: 22px; height: 22px; flex: none;
  }
  .brand-name {
    font-weight: 600;
    text-transform: uppercase;
    letter-spacing: 0.12em;
    line-height: 1.15;
  }
  .card-back .brand-mark { background: var(--white); }
  .card-back .brand-name { font-size: 24px; color: var(--white); }

  .services {
    list-style: none;
    margin-top: 46px;
  }
  .services li {
    position: relative;
    padding-left: 20px;
    font-size: 14px;
    font-weight: 600;
    text-transform: uppercase;
    letter-spacing: 0.06em;
    line-height: 1.75;
  }
  .services li::before {
    content: "";
    position: absolute; left: 0; top: 9px;
    width: 7px; height: 7px; border-radius: 50%;
    background: var(--white);
  }

  /* Front side */
  .card-front {
    left: 580px; top: 500px;
    background: var(--white);
  }
  .front-top {
    position: absolute; left: 0; top: 0; width: 100%; height: 178px;
    padding: 46px 40px 0 40px;
  }
  .card-front .brand-mark { background: var(--teal); width: 18px; height: 18px; }
  .card-front .brand-name { font-size: 19px; color: var(--teal); }
  .tagline {
    margin-top: 16px;
    font-size: 15px; font-weight: 700;
    color: var(--teal);
    letter-spacing: 0.01em;
  }
  .social {
    position: absolute; right: 28px; top: 146px;
    display: flex; align-items: center; gap: 8px;
    font-size: 13px; color: var(--teal);
  }
  .social-mark { width: 13px; height: 13px; background: var(--teal); border-radius: 2px; }

  .front-rule {
    position: absolute; left: 0; top: 174px; width: 100%; height: 4px;
    background: var(--rule);
  }
  .front-band {
    position: absolute; left: 0; top: 178px; width: 100%; height: 142px;
    background: var(--teal-deep);
    color: var(--white);
    padding: 24px 40px 0 40px;
    border-top: 4px solid var(--white);
  }
  .person-name {
    font-size: 22px; font-weight: 700;
    text-transform: uppercase; letter-spacing: 0.1em;
  }
  .person-role {
    font-size: 13px; color: var(--text-soft); margin-top: 2px;
  }
  .contact { list-style: none; margin-top: 12px; }
  .contact li {
    display: flex; align-items: center; gap: 10px;
    font-size: 14px; line-height: 1.7;
  }
  .contact svg { width: 14px; height: 14px; flex: none; }
</style>
</head>
<body>
<main class="canvas">

  <section class="card card-back" aria-label="Card back">
    <div class="brand">
      <span class="brand-mark"></span>
      <span class="brand-name">Harbourline<br>Electrical Solutions</span>
    </div>
    <ul class="services">
      <li>Data &amp; Communication</li>
      <li>LED Lighting &amp; Automation</li>
      <li>Electrical Construction &amp; Maintenance</li>
      <li>Life Safety Systems (Fire Alarm / Security)</li>
    </ul>
  </section>

  <section class="card card-front" aria-label="Card front">
    <div class="front-top">
      <div class="brand">
        <span class="brand-mark"></span>
        <span class="brand-name">Harbourline<br>Electrical Solutions</span>
      </div>
      <p class="tagline">Commercial Industrial Residential</p>
    </div>
    <div class="social">
      <span class="social-mark"></span>
      <span>@hlelectricalsolutions</span>
    </div>
    <div class="front-rule"></div>
    <div class="front-band">
      <h1 class="person-name">Marcus T. Hollings</h1>
      <p class="person-role">Project Manager</p>
      <ul class="contact">
        <li>
          <svg viewBox="0 0 24 24" aria-hidden="true"><path fill="#fff" d="M6.6 10.8a15.1 15.1 0 0 0 6.6 6.6l2.2-2.2c.3-.3.7-.4 1-.2 1.1.4 2.3.6 3.6.6.6 0 1 .4 1 1V20c0 .6-.4 1-1 1A17 17 0 0 1 3 4c0-.6.4-1 1-1h3.5c.6 0 1 .4 1 1 0 1.3.2 2.5.6 3.6.1.3 0 .7-.2 1z"/></svg>
          <span>(441) 555-0187</span>
        </li>
        <li>
          <svg viewBox="0 0 24 24" aria-hidden="true"><rect x="2.5" y="5" width="19" height="14" rx="1.5" fill="none" stroke="#fff" stroke-width="2"/><path d="M3 6l9 7 9-7" fill="none" stroke="#fff" stroke-width="2"/></svg>
          <span>hlelectricalsolutions@mailvento.com</span>
        </li>
      </ul>
    </div>
  </section>

</main>
</body>
</html>
```